We need a binder cover. I have attached a photo of what we want it ot look like but use our logo, graphic and colour scheme. The dimensions are”
11.5Hx10.5W – front cover
11.5Hx1.5W – side spine
The Website is www.marbletreeadvisory.ca
For keywords please use Dignity, Independence and Accessibility
As well, we are looking for 2 versions of letterhead .
1. Standard document layout to make table of contents,cover page (no address).
2. Standard letter head with address on the bottom of the page.
Our address is
418 Kestrel Lane East Unit 3 Suite 214
Oakville Ontario
K9T 4B7
Also want a CD labels for us,
1. With our logo and “Accessibility Standard for Customer Service – Staff Training Session” Power Point with Audio
2. With our logo and “Accessibility Standard for Customer Service – Staff Training Session” CD audio only format
3. With our logo and “ Copy of documentation for QBEX”

```html
<!DOCTYPE html>
<html lang="en">
<head>
<meta charset="utf-8">
<title>Marbletree Advisory – Letterhead Set</title>
<link rel="stylesheet" href="https://fonts.googleapis.com/css2?family=Arimo:wght@400;700&display=swap">
<style>
  :root {
    --bg: #e6e3de;
    --paper: #ffffff;
    --ink: #1f1f1f;
    --brand-red: #e3202a;
    --bar: #3c3c3c;
    --bar-text: #f2f2f2;
    --sign: #9a9a9a;
  }
  * { box-sizing: border-box; margin: 0; padding: 0; }
  html, body { width: 1200px; height: 771px; overflow: hidden; }
  body {
    background: var(--bg);
    font-family: "Arimo", Arial, sans-serif;
    color: var(--ink);
    position: relative;
  }
  .sheet {
    position: absolute;
    top: 72px;
    width: 456px;
    height: 626px;
    background: var(--paper);
    box-shadow: 0 2px 6px rgba(0,0,0,.18);
  }
  .sheet--contents { left: 96px; }
  .sheet--letter { left: 621px; }

  .brand {
    position: absolute;
    top: 30px;
    left: 32px;
    display: flex;
    align-items: center;
    gap: 7px;
  }
  .brand__mark { width: 28px; height: 28px; background: var(--brand-red); }
  .brand__name {
    font-weight: 700;
    font-size: 12px;
    line-height: 13px;
    color: var(--brand-red);
    letter-spacing: .2px;
  }

  .footer-bar {
    position: absolute;
    left: 0; right: 0; bottom: 0;
    height: 17px;
    background: var(--bar);
    display: flex;
    justify-content: flex-end;
    align-items: center;
    padding-right: 8px;
  }
  .footer-bar__url { color: var(--bar-text); font-size: 9.5px; margin-right: 12px; }
  .footer-bar__page {
    width: 16px; height: 17px;
    background: var(--brand-red);
    color: #fff;
    font-size: 9px;
    display: flex; align-items: center; justify-content: center;
  }

  .contents__title {
    position: absolute;
    top: 107px; left: 0; right: 0;
    text-align: center;
    font-weight: 700;
    font-size: 12.5px;
  }
  .contents__list {
    position: absolute;
    top: 151px; left: 40px;
    width: 393px;
    list-style: none;
    font-size: 8.9px;
    line-height: 12.4px;
  }
  .entry { display: flex; white-space: nowrap; }
  .entry--section { font-weight: 700; }
  .entry__num { width: 28px; flex: none; }
  .entry__title { flex: none; }
  .entry__dots {
    flex: 1; overflow: hidden;
    margin: 0 3px;
    font-weight: 400;
    letter-spacing: 0.5px;
  }
  .entry__dots::after { content: "...................................................................................................................................................................................."; }
  .entry__page { flex: none; font-weight: 400; }

  .letter {
    position: absolute;
    top: 124px; left: 32px;
    width: 393px;
    font-size: 8.5px;
    line-height: 12.1px;
  }
  .letter p { text-align: justify; margin-bottom: 12.1px; }
  .letter__signature {
    display: block;
    width: 62px; height: 34px;
    margin-top: 4px;
    background: linear-gradient(90deg, #fff, #d6d6d6 30%, #c9c9c9 70%, #fff);
    border-radius: 14px;
  }
  .letter-address {
    position: absolute;
    top: 582px; left: 32px;
    font-size: 8.5px;
    line-height: 12.1px;
  }
</style>
</head>
<body>

<section class="sheet sheet--contents">
  <div class="brand"><span class="brand__mark"></span><span class="brand__name">MARBLETREE<br>ADVISORY INC.</span></div>
  <h1 class="contents__title">TABLE OF CONTENTS</h1>
  <ul class="contents__list">
    <li class="entry entry--section"><span class="entry__title">SECTION A -- SOLICITATION/CONTRACT FORM</span><span class="entry__dots"></span><span class="entry__page">3</span></li>
    <li class="entry"><span class="entry__num">A.1</span><span class="entry__title">GENERAL INFORMATION</span><span class="entry__dots"></span><span class="entry__page">3</span></li>
    <li class="entry"><span class="entry__num">A.2</span><span class="entry__title">ISSUING OFFICE</span><span class="entry__dots"></span><span class="entry__page">3</span></li>
    <li class="entry"><span class="entry__num">A.3</span><span class="entry__title">RECEIPT OF PROPOSALS AND LATE SUBMISSIONS</span><span class="entry__dots"></span><span class="entry__page">3</span></li>
    <li class="entry"><span class="entry__num">A.4</span><span class="entry__title">NOTICE OF SET-ASIDE</span><span class="entry__dots"></span><span class="entry__page">4</span></li>
    <li class="entry"><span class="entry__num">A.5</span><span class="entry__title">BASIS FOR AWARD</span><span class="entry__dots"></span><span class="entry__page">4</span></li>
    <li class="entry entry--section"><span class="entry__title">SECTION B - SUPPLIES OR SERVICES AND PRICES/COSTS</span><span class="entry__dots"></span><span class="entry__page">5</span></li>
    <li class="entry"><span class="entry__num">B.1</span><span class="entry__title">SCOPE OF SERVICES</span><span class="entry__dots"></span><span class="entry__page">5</span></li>
    <li class="entry"><span class="entry__num">B.2</span><span class="entry__title">CONSIDERATION (FIXED PRICE SERVICES)</span><span class="entry__dots"></span><span class="entry__page">5</span></li>
    <li class="entry entry--section"><span class="entry__title">SECTION C – DESCRIPTION/SPECIFICATION/WORK STATEMENT</span><span class="entry__dots"></span><span class="entry__page">6</span></li>
    <li class="entry"><span class="entry__num">C.1</span><span class="entry__title">BACKGROUND</span><span class="entry__dots"></span><span class="entry__page">6</span></li>
    <li class="entry"><span class="entry__num">C.2</span><span class="entry__title">OVERVIEW</span><span class="entry__dots"></span><span class="entry__page">6</span></li>
    <li class="entry"><span class="entry__num">C.3</span><span class="entry__title">STATEMENT OF WORK</span><span class="entry__dots"></span><span class="entry__page">6</span></li>
    <li class="entry entry--section"><span class="entry__title">SECTION D – PACKAGING AND MARKING</span><span class="entry__dots"></span><span class="entry__page">8</span></li>
    <li class="entry"><span class="entry__num">D.1</span><span class="entry__title">PACKAGING AND MARKING INSTRUCTIONS</span><span class="entry__dots"></span><span class="entry__page">8</span></li>
    <li class="entry entry--section"><span class="entry__title">SECTION E -- INSPECTION AND ACCEPTANCE</span><span class="entry__dots"></span><span class="entry__page">9</span></li>
    <li class="entry"><span class="entry__num">E.1</span><span class="entry__title">52.252-02 CLAUSES INCORPORATED BY REFERENCE (FEB 1998)</span><span class="entry__dots"></span><span class="entry__page">9</span></li>
    <li class="entry"><span class="entry__num">E.2</span><span class="entry__title">ACCEPTANCE OF DELIVERABLES</span><span class="entry__dots"></span><span class="entry__page">9</span></li>
    <li class="entry entry--section"><span class="entry__title">SECTION F -- DELIVERIES OR PERFORMANCE</span><span class="entry__dots"></span><span class="entry__page">10</span></li>
    <li class="entry"><span class="entry__num">F.1</span><span class="entry__title">52.252-02 CLAUSES INCORPORATED BY REFERENCE (FEB 1998)</span><span class="entry__dots"></span><span class="entry__page">10</span></li>
    <li class="entry"><span class="entry__num">F.2</span><span class="entry__title">DELIVERY SCHEDULE</span><span class="entry__dots"></span><span class="entry__page">10</span></li>
    <li class="entry"><span class="entry__num">F.3</span><span class="entry__title">REPORTING REQUIREMENTS</span><span class="entry__dots"></span><span class="entry__page">10</span></li>
    <li class="entry entry--section"><span class="entry__title">SECTION G -- CONTRACT ADMINISTRATION DATA</span><span class="entry__dots"></span><span class="entry__page">11</span></li>
    <li class="entry"><span class="entry__num">G.1</span><span class="entry__title">INVOICE AND BILLING INFORMATION</span><span class="entry__dots"></span><span class="entry__page">11</span></li>
    <li class="entry"><span class="entry__num">G.2</span><span class="entry__title">PAYMENT INFORMATION</span><span class="entry__dots"></span><span class="entry__page">11</span></li>
    <li class="entry"><span class="entry__num">G.3</span><span class="entry__title">COTR DESIGNATION AND AUTHORITY</span><span class="entry__dots"></span><span class="entry__page">11</span></li>
    <li class="entry"><span class="entry__num">G.4</span><span class="entry__title">CONTRACTING OFFICER'S AUTHORITY</span><span class="entry__dots"></span><span class="entry__page">12</span></li>
    <li class="entry"><span class="entry__num">G.5</span><span class="entry__title">CONTRACTOR PERFORMANCE EVALUATIONS</span><span class="entry__dots"></span><span class="entry__page">13</span></li>
    <li class="entry entry--section"><span class="entry__title">SECTION H – SPECIAL CONTRACT REQUIREMENTS</span><span class="entry__dots"></span><span class="entry__page">14</span></li>
    <li class="entry entry--section"><span class="entry__title">SECTION I -- CONTRACT CLAUSES</span><span class="entry__dots"></span><span class="entry__page">15</span></li>
    <li class="entry"><span class="entry__num">I.1</span><span class="entry__title">52.252-02 CLAUSES INCORPORATED BY REFERENCE (FEB 1998)</span><span class="entry__dots"></span><span class="entry__page">15</span></li>
    <li class="entry entry--section"><span class="entry__title">SECTION J – LIST OF ATTACHMENTS</span><span class="entry__dots"></span><span class="entry__page">17</span></li>
    <li class="entry entry--section"><span class="entry__title">SECTION K -- REPRESENTATIONS, CERTIFICATIONS AND OTHER STATEMENTS</span></li>
    <li class="entry entry--section"><span class="entry__title">OF OFFERORS</span><span class="entry__dots"></span><span class="entry__page">18</span></li>
  </ul>
  <footer class="footer-bar"><span class="footer-bar__url">www.marbletreeadvisory.ca</span><span class="footer-bar__page">1</span></footer>
</section>

<section class="sheet sheet--letter">
  <div class="brand"><span class="brand__mark"></span><span class="brand__name">MARBLETREE<br>ADVISORY INC.</span></div>
  <div class="letter">
    <p>Mr. Peter Lindqvist,</p>
    <p>Lorem ipsum dolor sit amet, consectetuer adipiscing elit, sed diam nonummy nibh euismod tincidunt ut laoreet dolore magna aliquam erat volutpat. Ut wisi enim ad minim veniam, quis nostrud exerci tation ullamcorper suscipit lobortis nisl ut aliquip ex ea commodo consequat. Duis autem vel eum iriure dolor in hendrerit in vulputate velit esse molestie consequat, vel illum dolore eu feugiat nulla facilisis at vero eros et accumsan et iusto odio dignissim qui blandit praesent luptatum zzril delenit augue duis dolore te feugait nulla facilisi. Nam liber tempor cum soluta nobis eleifend option congue nihil imperdiet doming id quod mazim placerat facer possim assum. Typi non habent claritatem insitam; est usus legentis in iis qui facit eorum claritatem. Investigationes demonstraverunt lectores legere me lius quod ii legunt saepius. Claritas est etiam processus dynamicus, qui sequitur mutationem consuetudium lectorum. Mirum est notare quam littera gothica, quam nunc putamus parum claram, anteposuerit litterarum formas humanitatis per seacula quarta decima et quinta decima. Eodem modo typi, qui nunc nobis videntur parum clari, fiant sollemnes in futurum.</p>
    <p>Lorem ipsum olor sit amet, consectetuer adipiscing elit, sed diam nonummy nibh euismod tincidunt ut laoreet dolore magna aliquam erat volutpat. Ut wisi enim ad minim veniam, quis nostrud exerci tation ullamcorper suscipit lobortis nisl ut aliquip ex ea commodo consequat. Duis autem vel eum iriure dolor in hendrerit in vulputate velit esse molestie consequat, vel illum dolore eu feugiat nulla facilisis at vero eros et accumsan et iusto odio dignissim qui blandit praesent luptatum zzril delenit augue duis dolore te feugait nulla facilisi. Nam liber tempor cum soluta nobis eleifend option congue nihil imperdiet doming id quod mazim placerat facer possim assum. Typi non habent claritatem insitam; est usus legentis in iis qui facit eorum claritatem. Investigationes demonstraverunt lectores legere me lius quod ii legunt saepius. Claritas est etiam processus dynamicus, qui sequitur mutationem consuetudium lectorum. Mirum est notare quam littera gothica, quam nunc putamus parum claram, anteposuerit litterarum formas humanitatis per seacula quarta decima et quinta decima. Eodem modo typi, qui nunc nobis videntur parum clari, fiant sollemnes in futurum.</p>
    <p style="margin-bottom:0">Yours greatful,<br>Martin Halloway</p>
    <span class="letter__signature" role="img" aria-label="Handwritten signature of Martin Halloway"></span>
  </div>
  <address class="letter-address" style="font-style:normal">418 Kestrel Lane East Unit 3 Suite 214<br>Oakville Ontario, K9T 4B7</address>
  <footer class="footer-bar"><span class="footer-bar__url">www.marbletreeadvisory.ca</span><span class="footer-bar__page">1</span></footer>
</section>

</body>
</html>
```